Fern Haven Premier Cleaning Service , Inc wants to make the buck so make it happen = )

I need a postcard design for my cleaning company. I have full ownership and 15+ years experience. At this time we take care of residential clients as well as commercial clients. Mainly offices. I do plan to expand my business in the commercial aspect. My experience is that we compete with franchise companies and my company deliveries a higher quality of work.
I already have a logo designed which I would like to use. Basically we do high quality, detail oriented work not just the first time to get the client but years and years ahead.

Target Market(s)

Commercial Offices

Industry/Entity Type

Residential

Font styles to use
Serif
Sans Serif

Colors
9bcb3c
ec1f27
33a6d7
3075b4
f78f20

Requirements
Must have
• focusing on quality, reliability, wants to stand of the crowd
Nice to have
• anything that makes the sale
Should not have
• too much general cleaning company adds

```html
<!DOCTYPE html>
<html lang="en">
<head>
<meta charset="utf-8">
<title>Fern Haven Premier Cleaning Service, Inc – Postcard</title>
<link rel="stylesheet" href="https://fonts.googleapis.com/css2?family=Arimo:wght@400;700&display=swap">
<style>
  :root {
    --red: #ec1f27;
    --sky: #33a6d7;
    --blue: #3075b4;
    --green: #9bcb3c;
    --orange: #f78f20;
    --ink: #3a3a3a;
    --paper: #ffffff;
    --stage: #f2f2f2;
  }
  * { box-sizing: border-box; margin: 0; padding: 0; }
  html, body {
    width: 1200px; height: 731px; overflow: hidden;
    background: var(--stage);
    font-family: "Arimo", Arial, sans-serif;
  }
  .postcard {
    position: absolute; left: 25px; top: 15px;
    width: 1150px; height: 700px;
    background: var(--paper);
    box-shadow: 0 2px 10px rgba(0,0,0,.12);
    overflow: hidden;
  }
  .swoosh { position: absolute; left: 0; top: 0; }
  .offer {
    position: absolute; left: 50px; top: 90px; width: 510px;
    color: var(--ink);
  }
  .section-title {
    color: var(--red); font-weight: 400; font-size: 20px; line-height: 24px;
    letter-spacing: .5px; text-align: center; margin-bottom: 10px;
  }
  .area-title {
    color: var(--sky); font-weight: 400; font-size: 18px; line-height: 22px;
    letter-spacing: .5px; margin-bottom: 4px;
  }
  .area-text {
    font-size: 13px; line-height: 19.5px; letter-spacing: .4px;
    margin-bottom: 12px;
  }
  .section-title.commercial { margin-top: 6px; }
  .photo-row {
    position: absolute; left: 0; top: 0; width: 600px; height: 700px;
    pointer-events: none;
  }
  .photo {
    position: absolute; border-radius: 50%;
    border: 3px solid #fff; box-shadow: 0 1px 4px rgba(0,0,0,.25);
  }
  .photo.bedroom { left: 60px;  top: 515px; width: 68px; height: 68px; background: radial-gradient(circle at 40% 40%, #c77a4e, #5a2a1a); }
  .photo.suite   { left: 138px; top: 500px; width: 80px; height: 80px; background: radial-gradient(circle at 50% 45%, #e6d6bd, #8c6b4a); }
  .photo.lounge  { left: 232px; top: 500px; width: 66px; height: 66px; background: radial-gradient(circle at 50% 50%, #b0704a, #4a2616); }
  .photo.tower   { left: 314px; top: 490px; width: 72px; height: 72px; background: linear-gradient(160deg, #4a7fd0, #cfe0f2 60%, #6a8a4a); }
  .photo.office  { left: 404px; top: 488px; width: 60px; height: 60px; background: radial-gradient(circle at 50% 50%, #d8dde0, #7a8a94); }
  .brand {
    position: absolute; left: 66px; top: 594px;
    display: flex; align-items: center; gap: 10px;
  }
  .brand-mark { width: 30px; height: 30px; border-radius: 50%; background: var(--green); flex: none; }
  .brand-name { color: var(--blue); font-size: 17px; font-weight: 700; line-height: 1.15; }
  .mailing {
    position: absolute; left: 600px; top: 30px; width: 520px; height: 300px;
  }
  .contact { position: absolute; left: 20px; top: 60px; color: #111; font-style: normal; }
  .contact-title { font-size: 17px; font-weight: 700; letter-spacing: .5px; margin-bottom: 6px; }
  .contact-line { font-size: 12.5px; font-weight: 700; line-height: 1.5; padding-left: 10px; letter-spacing: .3px; }
  .indicia {
    position: absolute; right: 20px; top: 0; width: 90px; height: 70px;
    border: 1px solid #333; display: flex; align-items: center; justify-content: center;
    text-align: center; font-size: 7px; line-height: 1.3; color: #222;
  }
</style>
</head>
<body>
  <main class="postcard">
    <svg class="swoosh" width="1150" height="700" viewBox="0 0 1150 700" aria-hidden="true">
      <path d="M0 0 H600 C420 28 200 55 0 95 Z" fill="var(--red)"/>
      <path d="M0 700 H600 V590 C480 650 250 680 0 690 Z" fill="var(--red)"/>
    </svg>

    <section class="offer">
      <h2 class="section-title">RESIDENTIAL CLEANING</h2>
      <h3 class="area-title">ALL LIVING AREAS</h3>
      <p class="area-text">Remove all cobwebs - Clean ceiling fans, dust light fixtures - Clean light switch plates - Clean smudges from doors - Dust blinds, window sills - Dust picture frames, knick-knacks - Dust furniture - Vacuum upholstered furniture - Clean baseboards - Straighten up - Remove trash - Vacuum</p>
      <h3 class="area-title">KITCHEN</h3>
      <p class="area-text">Remove cob-webs - Dust ceiling fans, light fixtures - Wipe cabinets and drawers exterior - Clean light switch plates - Remove smudges from doors - Clean blinds and window sills - Counters and backsplash cleaned and sanitized - Sink cleaned and sanitized - Microwave cleaned inside -</p>
      <h2 class="section-title commercial">COMMERCIAL CLEANING</h2>
      <h3 class="area-title">WE PROVIDE SERVICES TO:</h3>
      <p class="area-text">Apartment Buildings • Professional Offices • Property Management Companies • Realtors • Financial Institutions / Banks • Hair Salons / Nail Salons / Spas</p>
    </section>

    <div class="photo-row">
      <div class="photo bedroom" role="img" aria-label="Photo of a cleaned bedroom"></div>
      <div class="photo suite" role="img" aria-label="Photo of a bright hotel-style suite"></div>
      <div class="photo lounge" role="img" aria-label="Photo of a wood-panelled lounge"></div>
      <div class="photo tower" role="img" aria-label="Photo of a modern office building"></div>
      <div class="photo office" role="img" aria-label="Photo of an office interior"></div>
    </div>

    <div class="brand">
      <span class="brand-mark" aria-hidden="true"></span>
      <span class="brand-name">Fern Haven<br>Premier Cleaning Service , Inc</span>
    </div>

    <section class="mailing">
      <div class="indicia">First Class Mail<br>U.S. Postage<br>PAID<br>PERMIT NO</div>
      <address class="contact">
        <p class="contact-title">CONTACT US TODAY :</p>
        <p class="contact-line">P.O. BOX 4821</p>
        <p class="contact-line">ALDER GROVE, SC 29870</p>
        <p class="contact-line">TEL : 555-014-2277</p>
        <p class="contact-line">Email Us : hello@fernhavenclean.com</p>
      </address>
    </section>
  </main>
</body>
</html>
```